Varnik Holdings — Business Card Design Brief
Overview
Design a double-sided business card for Varnik Holdings that highlights our two service arms: Varnik Communications (telecommunications) and Varnik Energy (business energy solutions). The card should feel smart and stand out when handed to clients.

Objectives
Showcase our areas of specialty clearly.
Reflect the overall Varnik / Varnik Holdings brand while acknowledging both arms.
Explore using both logos (Communications + Energy) or one unified logo, depending on the design.

Deliverables
One double-sided business card design (front + back).

Content & Copy
Front (preferred): Logo: Varnik / Varnik Holdings
Descriptor: Business Communications | Business Energy
Back:My contact details and company details
Core products: Business Mobile • Telephony • Internet • Business Energy Solutions

Brand & Visual Direction
We have a group logo currently tailored more toward telecoms, plus a separate Varnik Energy logo.
Please explore layouts that use both logos or just one, whichever works best.
Color: I wouldn't mind seeing an option using our the Blue/Purple gradient from our website (varnik-example.co.uk), but also open to non-gradient approaches and other colours..

Overall look: Smart, modern, and distinctive.
Format & Print Specs
Double-sided business card format. (Use a standard size

Must-Haves
Front: Varnik wording or Varnik Holdings wording with atleast 1 logo also on front “Business Communications | Business Energy.”

Back: Contact + company details and core products.
A design that stands out while remaining professional.

Nice-to-Have Options
A gradient version using our site’s Blue/Purple gradient.
A non-gradient version.
A dual-logo treatment versus a single-logo treatment.

Thanks
Owen

```html
<!DOCTYPE html>
<html lang="en">
<head>
<meta charset="utf-8">
<title>Varnik Holdings – Business Card</title>
<link href="https://fonts.googleapis.com/css2?family=Poppins:wght@700&family=Arimo:wght@400&display=swap" rel="stylesheet">
<style>
  :root {
    --page-bg: #e6e6e6;
    --navy: #1c1a6e;
    --blue: #1f7de0;
    --sky: #0bb5e3;
    --deep: #0a5bd3;
    --text-grey: #3c3c3c;
    --rule: #c9c9c9;
    --white: #ffffff;
  }
  * { box-sizing: border-box; margin: 0; padding: 0; }
  html, body { width: 1200px; height: 1200px; overflow: hidden; }
  body { background: var(--page-bg); position: relative; font-family: "Arimo", Arial, sans-serif; }

  .card { position: absolute; width: 689px; height: 394px; overflow: hidden; }
  .card-front { left: 267px; top: 159px; background: var(--white); }
  .card-back { left: 262px; top: 653px; background: linear-gradient(180deg, var(--sky) 0%, var(--deep) 100%); }

  .front-deco { position: absolute; left: -15px; top: 170px; width: 200px; height: 200px; border-radius: 50%; border: 16px solid rgba(31,125,224,0.06); }

  .brand { position: absolute; right: 45px; top: 118px; display: flex; align-items: center; gap: 12px; }
  .brand-dot { width: 30px; height: 30px; border-radius: 50%; background: var(--blue); }
  .brand-name { font-family: "Poppins", Arial, sans-serif; font-weight: 700; font-size: 43px; line-height: 1; color: var(--navy); letter-spacing: 0.5px; }

  .person { position: absolute; left: 48px; top: 222px; }
  .person-name { font-family: "Poppins", Arial, sans-serif; font-weight: 700; font-size: 26px; line-height: 1; color: var(--navy); letter-spacing: 0.3px; }
  .person-role { font-size: 16px; color: var(--blue); margin-top: 6px; }

  .contact-list { position: absolute; left: 48px; top: 289px; list-style: none; }
  .contact-list li { display: flex; align-items: center; height: 21px; font-size: 16px; color: var(--text-grey); }
  .contact-list svg { width: 14px; height: 14px; margin-right: 7px; fill: var(--navy); flex: none; }

  .address, .products { position: absolute; right: 45px; text-align: right; font-size: 16px; line-height: 21px; color: var(--text-grey); }
  .address { top: 226px; }
  .products { top: 289px; }
  .divider { position: absolute; left: 48px; right: 45px; top: 281px; height: 1px; background: var(--rule); }

  .band-bar { position: absolute; left: 0; bottom: 0; width: 430px; height: 14px; background: linear-gradient(90deg, var(--deep), var(--sky) 70%, var(--deep)); clip-path: polygon(0 0, 100% 0, 96% 100%, 0 100%); }
  .band-web { position: absolute; right: 0; bottom: 0; width: 274px; height: 34px; background: var(--navy); clip-path: polygon(26px 0, 100% 0, 100% 100%, 0 100%); color: var(--white); font-size: 16px; display: flex; align-items: center; justify-content: flex-end; padding-right: 14px; }

  .arm { position: absolute; top: 150px; width: 300px; text-align: center; color: var(--white); }
  .arm-comms { left: 50px; }
  .arm-energy { left: 333px; }
  .arm-mark { display: flex; align-items: center; justify-content: center; gap: 12px; height: 70px; }
  .arm-dot { width: 34px; height: 34px; border-radius: 50%; background: var(--white); }
  .arm-name { font-family: "Poppins", Arial, sans-serif; font-weight: 700; font-size: 38px; line-height: 1; color: var(--white); }
  .arm-label { font-size: 16px; letter-spacing: 0.2px; margin-top: 40px; }
  .back-divider { position: absolute; left: 345px; top: 114px; width: 1px; height: 167px; background: rgba(255,255,255,0.75); }
</style>
</head>
<body>
  <section class="card card-front" aria-label="Card front">
    <div class="front-deco"></div>

    <div class="brand">
      <span class="brand-dot"></span>
      <span class="brand-name">VARNIK</span>
    </div>

    <div class="person">
      <p class="person-name">MARCUS HALE</p>
      <p class="person-role">President</p>
    </div>

    <ul class="contact-list">
      <li><svg viewBox="0 0 24 24"><path d="M6.6 10.8a15.1 15.1 0 0 0 6.6 6.6l2.2-2.2c.3-.3.7-.4 1-.2 1.1.4 2.3.6 3.6.6.6 0 1 .4 1 1V20c0 .6-.4 1-1 1A17 17 0 0 1 3 4c0-.6.4-1 1-1h3.5c.6 0 1 .4 1 1 0 1.3.2 2.5.6 3.6.1.3 0 .7-.2 1z"/></svg>555-214-7730</li>
      <li><svg viewBox="0 0 24 24"><path d="M7 1h10a2 2 0 0 1 2 2v18a2 2 0 0 1-2 2H7a2 2 0 0 1-2-2V3a2 2 0 0 1 2-2zm0 3v14h10V4zm5 15.5a1 1 0 1 0 0 2 1 1 0 0 0 0-2z"/></svg>555-382-9161</li>
      <li><svg viewBox="0 0 24 24"><path d="M2 5h20v14H2zm2 2v.5l8 5 8-5V7l-8 5z"/></svg>info@varnik-example.co.uk</li>
    </ul>

    <p class="address">4120 Larkspur Road<br>Halden, Canada 20417</p>
    <div class="divider"></div>
    <p class="products">Business Mobile<br>Telephony • Internet<br>Business Energy Solutions</p>

    <div class="band-bar"></div>
    <div class="band-web">www.varnik-example.co.uk</div>
  </section>

  <section class="card card-back" aria-label="Card back">
    <div class="arm arm-comms">
      <div class="arm-mark"><span class="arm-dot"></span><span class="arm-name">VARNIK</span></div>
      <p class="arm-label">BUSINESS COMMUNICATIONS</p>
    </div>
    <div class="back-divider"></div>
    <div class="arm arm-energy">
      <div class="arm-mark"><span class="arm-dot"></span><span class="arm-name">VARNIK</span></div>
      <p class="arm-label">BUSINESS ENERGY</p>
    </div>
  </section>
</body>
</html>
```